KRL Stationery Design Project

Dear Designers,
We need a new stationery design for company to match our new logo.
Designers should provide a design for the following:
1. Business Card: 3.5x2 Inches.
2. Letterhead: A4 size.
3. Envelops: 25x35.5 Cm.
You can keep the Arabic name at the bottom of the logo Or you can use the separate attached Arabic Name.
Please refer to the attached logo guide for design information.
Sample Business Card information:
Name: Tarek Sowan
Position: Operation Manager
Tel: +966 920007164 Ex. 500
Fax: +966 (3)8842617
Mob: +966 (5)00263817
email: tarek@krl-example.com.sa
URL: www.krl-example.com.sa
Address:
Nakheel Heights, Suite 718
Zayed bin Omar Str.
Khobar, 31847
Saudi Arabia
Updates
Dear All,
Please note, we had uploaded our logo along with Arabic writing in Adobe illustrator format (.ai).
Regards,
Karim
Dear All,
A sample data for the business card had been added as per your request.
Regards,
Karim

```html
<!DOCTYPE html>
<html lang="en">
<head>
<meta charset="utf-8">
<title>KRL Business Card</title>
<link href="https://fonts.googleapis.com/css2?family=Ubuntu:wght@400;500;700&display=swap" rel="stylesheet">
<style>
  :root {
    --backdrop: #e6e6e6;
    --card: #ffffff;
    --navy: #0d2c4f;
    --grey: #9b9b9b;
    --ink: #555a60;
    --white: #ffffff;
  }
  * { box-sizing: border-box; margin: 0; padding: 0; }
  html, body {
    width: 1200px; height: 472px; overflow: hidden;
    background: var(--backdrop);
    font-family: "Ubuntu", sans-serif;
  }
  .stage { position: relative; width: 1200px; height: 472px; }
  .card {
    position: absolute; top: 84px;
    width: 525px; height: 298px;
    background: var(--card);
    border-radius: 14px;
    overflow: hidden;
  }
  .card--front { left: 58px; }
  .card--back { left: 605px; }

  .brand {
    position: absolute;
    display: flex; align-items: center; gap: 14px;
    color: var(--navy);
    font-weight: 700;
    letter-spacing: 2px;
    line-height: 1;
  }
  .card--front .brand { left: 46px; top: 50px; font-size: 62px; }
  .card--back .brand { left: 30px; top: 58px; font-size: 64px; }
  .brand__dot {
    width: 22px; height: 22px; border-radius: 50%;
    background: var(--grey);
  }

  .vehicle-art {
    position: absolute; top: 136px; left: 337px;
    width: 157px; height: 66px;
    background: linear-gradient(90deg, rgba(13,44,79,0.15), var(--navy));
  }

  .band {
    position: absolute; left: 0; right: 0; top: 202px; height: 36px;
    background: var(--navy);
    color: var(--white);
    display: flex; align-items: center;
  }
  .card--front .band { padding-left: 34px; }
  .band__name { font-weight: 700; font-size: 17px; text-transform: uppercase; letter-spacing: 0.3px; }
  .band__title { font-size: 14px; margin-left: 6px; }
  .card--back .band { padding-left: 118px; font-size: 13.5px; letter-spacing: 0.3px; }

  .contacts {
    position: absolute; left: 35px; top: 246px;
    display: flex; align-items: stretch;
    font-size: 13.5px; line-height: 17px; color: var(--ink);
  }
  .contacts__group { padding-right: 10px; }
  .contacts__group + .contacts__group {
    border-left: 1px solid var(--ink);
    padding-left: 9px;
  }
  .contacts__row { display: flex; align-items: center; gap: 6px; white-space: nowrap; }
  .icon { width: 10px; height: 10px; flex: none; }
</style>
</head>
<body>
<main class="stage">

  <section class="card card--front" aria-label="Business card front">
    <div class="brand"><span class="brand__name">KRL</span><span class="brand__dot"></span></div>

    <div class="vehicle-art" role="img" aria-label="Illustration of a tracked truck with signal antenna"></div>

    <div class="band">
      <span class="band__name">Your Name,</span>
      <span class="band__title">Title</span>
    </div>

    <div class="contacts">
      <div class="contacts__group">
        <div class="contacts__row">Street Name, City, State</div>
        <div class="contacts__row">City Zip Code 000 000</div>
      </div>
      <div class="contacts__group">
        <div class="contacts__row">
          <svg class="icon" viewBox="0 0 10 10" aria-hidden="true"><path d="M2 1 L4 1 L4.6 3 L3.4 4 Q4.5 6 6 6.6 L7 5.4 L9 6 L9 8 Q5 9 1.5 4.5 Q1 2.5 2 1Z" fill="#555a60"/></svg>
          123-456-7890
        </div>
        <div class="contacts__row">
          <svg class="icon" viewBox="0 0 10 10" aria-hidden="true"><path d="M2 5 L3 2.5 H7 L8 5 V8 H2Z" fill="#555a60"/><circle cx="3.3" cy="8.3" r="1" fill="#555a60"/><circle cx="6.7" cy="8.3" r="1" fill="#555a60"/></svg>
          123-456-7890
        </div>
      </div>
      <div class="contacts__group">
        <div class="contacts__row">
          <svg class="icon" viewBox="0 0 10 10" aria-hidden="true"><rect x="1" y="2.5" width="8" height="5.5" fill="#555a60"/><path d="M1 2.5 L5 5.5 L9 2.5" fill="none" stroke="#fff" stroke-width="0.8"/></svg>
          info@krl-example.com
        </div>
        <div class="contacts__row">
          <svg class="icon" viewBox="0 0 10 10" aria-hidden="true"><circle cx="5" cy="5" r="4" fill="#555a60"/><path d="M1 5h8M5 1v8" stroke="#fff" stroke-width="0.6"/></svg>
          www.krl-example.com
        </div>
      </div>
    </div>
  </section>

  <section class="card card--back" aria-label="Business card back">
    <div class="brand"><span class="brand__name">KRL</span><span class="brand__dot"></span></div>

    <div class="vehicle-art" role="img" aria-label="Illustration of a tracked truck with signal antenna"></div>

    <div class="band">www.krl-example.com</div>
  </section>

</main>
</body>
</html>
```